Varnex Consulting Business card design.

See our website www.varnexconsulting.example which will give you a good idea of what we are about. The font is called 'Play'.

I'd like a standout business card in keeping with the themes and branding on the website

Target Market(s)

professionals. HR directors

Industry/Entity Type

Business

Contact Information for Business Card

Varnex Consulting PO Box 3172 Merrowdale NSW 2291 1300 485 193 Gavin Threlkeld Principal email: career@varnexconsulting.example ABN: 71203948865

Font styles to use
Other font styles liked:
• Play

Requirements
Must have
• Must have same design colours and branding as website.
• On back I'd prefer a list of the things we do which appears below the name at the header on the website

```html
<!DOCTYPE html>
<html lang="en">
<head>
<meta charset="utf-8">
<title>Varnex Consulting – Business Card</title>
<link rel="stylesheet" href="https://fonts.googleapis.com/css2?family=Play:wght@400;700&display=swap">
<style>
  :root {
    --stage: #e8e5e0;
    --navy-deep: #07192b;
    --navy: #10304a;
    --navy-soft: #274a66;
    --sky-deep: #1466cc;
    --sky: #2f8fe4;
    --sky-light: #9ccbef;
    --cyan: #3dc3ee;
    --cyan-bright: #5fd2f5;
    --band-light: #34b2e8;
    --band-pale: #9fdcf6;
    --white: #ffffff;
    --rule: #e9eef3;
  }
  * { box-sizing: border-box; margin: 0; padding: 0; }
  html, body {
    width: 1200px; height: 902px; overflow: hidden;
    background: var(--stage);
    font-family: "Play", sans-serif;
  }
  .stage {
    position: relative; width: 1200px; height: 902px;
    display: flex; align-items: center; justify-content: center; gap: 40px;
  }
  .card {
    position: relative; width: 540px; height: 330px; overflow: hidden;
    border-radius: 3px;
    box-shadow: 0 10px 28px rgba(0,0,0,.22), 0 2px 6px rgba(0,0,0,.15);
  }

  /* front */
  .card-front { background: var(--navy); }
  .hero-photo {
    position: absolute; left: 0; top: 0; width: 100%; height: 214px;
    background: linear-gradient(135deg, var(--sky-deep) 0%, var(--sky) 55%, var(--sky-light) 100%);
  }
  .front-band {
    position: absolute; left: 0; bottom: 0; width: 100%; height: 116px;
    background: linear-gradient(90deg, var(--navy-soft) 0%, var(--navy) 55%, var(--navy-deep) 100%);
    padding: 28px 0 0 44px;
  }

  .wordmark {
    font-weight: 400; color: var(--white);
    letter-spacing: 1px; line-height: 1; text-transform: uppercase;
    white-space: nowrap;
  }
  .front-band .wordmark, .back-header .wordmark { font-size: 36px; }
  .services {
    margin-top: 10px; color: var(--cyan);
    font-size: 11.5px; letter-spacing: .6px; white-space: nowrap;
  }
  .services .sep { color: var(--band-pale); margin: 0 4px; }

  /* back */
  .card-back { background: var(--band-light); }
  .back-header {
    position: absolute; left: 0; top: 0; width: 100%; height: 176px;
    background: linear-gradient(160deg, var(--navy-soft) 0%, var(--navy) 40%, var(--navy-deep) 100%);
    padding: 72px 0 0 44px;
  }
  .divider-stripe {
    position: absolute; left: 0; top: 176px; width: 100%; height: 10px;
    background: var(--rule);
  }
  .contact-band {
    position: absolute; left: 0; top: 186px; width: 100%; height: 144px;
    background: linear-gradient(100deg, var(--band-light) 0%, #2fa7e2 50%, var(--cyan-bright) 100%);
    display: flex; align-items: stretch;
  }
  .person {
    width: 262px; padding: 60px 0 0 44px; color: var(--white);
  }
  .person-name { font-size: 24px; font-weight: 400; line-height: 1.05; white-space: nowrap; }
  .person-role { font-size: 18px; line-height: 1.1; }
  .contact-rule {
    width: 1px; margin: 14px 0 18px; background: rgba(255,255,255,.8);
  }
  .contact-list {
    list-style: none; padding: 16px 0 0 14px; color: var(--white);
    font-size: 13px; line-height: 1; white-space: nowrap;
  }
  .contact-list li { display: flex; align-items: center; gap: 8px; height: 24px; }
  .contact-list .abn { font-size: 15px; margin-bottom: 4px; }
  .icon {
    width: 14px; height: 14px; flex: none; border-radius: 2px;
    background: var(--white); display: flex; align-items: center; justify-content: center;
  }
  .icon svg { width: 10px; height: 10px; fill: var(--band-light); }
</style>
</head>
<body>
<main class="stage">

  <section class="card card-front" aria-label="Business card front">
    <div class="hero-photo" role="img" aria-label="Photograph of a snowboarder in mid-air above a snowy mountain peak against a bright blue sky"></div>
    <div class="front-band">
      <h1 class="wordmark">Varnex Consulting</h1>
      <p class="services">Search &amp; Select<span class="sep">|</span>Career<span class="sep">|</span>Coaching<span class="sep">|</span>Leadership<span class="sep">|</span>Outplacement</p>
    </div>
  </section>

  <section class="card card-back" aria-label="Business card back">
    <div class="back-header">
      <h2 class="wordmark">Varnex Consulting</h2>
      <p class="services">Search &amp; Select<span class="sep">|</span>Career<span class="sep">|</span>Coaching<span class="sep">|</span>Leadership<span class="sep">|</span>Outplacement</p>
    </div>
    <div class="divider-stripe"></div>
    <div class="contact-band">
      <div class="person">
        <p class="person-name">Gavin Threlkeld</p>
        <p class="person-role">Principal</p>
      </div>
      <div class="contact-rule"></div>
      <ul class="contact-list">
        <li class="abn">ABN: 71203948865</li>
        <li>
          <span class="icon"><svg viewBox="0 0 10 10"><path d="M2 0.5 L3.8 2.6 L2.9 3.6 Q4 5.8 6.4 7.1 L7.4 6.2 L9.5 8 L8.2 9.5 Q3.5 8.8 0.5 1.8 Z"/></svg></span>
          1300 485 193
        </li>
        <li>
          <span class="icon"><svg viewBox="0 0 10 10"><path d="M0.5 2 H9.5 V8 H0.5 Z M1.2 2.6 L5 5.4 L8.8 2.6" stroke="#34b2e8" stroke-width=".8" fill="none"/></svg></span>
          career@varnexconsulting.example
        </li>
        <li>
          <span class="icon"><svg viewBox="0 0 10 10"><path d="M5 0.5 A3.2 3.2 0 0 1 8.2 3.7 C8.2 6 5 9.5 5 9.5 C5 9.5 1.8 6 1.8 3.7 A3.2 3.2 0 0 1 5 0.5 Z M5 2.6 A1.1 1.1 0 1 0 5 4.8 A1.1 1.1 0 1 0 5 2.6 Z"/></svg></span>
          PO Box 3172 Merrowdale NSW 2291
        </li>
      </ul>
    </div>
  </section>

</main>
</body>
</html>
```